Business Card- Can you make it cool vs boring!

Need a refresh on my business card! Want it to be modern but simple, classic and a pop of coolness! we do senior living and it is boring. but that doesn't mean our business card have to look boring! Open to two sided cards. our website is www.Dunmere-PK.com

Target Market(s)

capital market

Industry/Entity Type

senior housing/ real estate

Contact Information for Business Card

logo/ name/ cell/ address/ www.Dunmere-PK.com/ space for a QR code

Requirements
Must have
• maybe a QR code (do not make prominent I may not use the QR so design where it can be taken out) that link to more about us/ landing page. needs to be modern but clean
Should not have
• clip art or script

```html
<!DOCTYPE html>
<html lang="en">
<head>
<meta charset="utf-8">
<title>Dunmere Living – Business Card</title>
<link href="https://fonts.googleapis.com/css2?family=Poppins:wght@400;500;600&display=swap" rel="stylesheet">
<style>
  :root {
    --backdrop: #e2e7e9;
    --rust: #ad5127;
    --charcoal: #222226;
    --band: #1f1f23;
    --white: #ffffff;
    --muted: #8a8a90;
  }
  * { margin: 0; padding: 0; box-sizing: border-box; }
  html, body {
    width: 1200px; height: 960px; overflow: hidden;
    background: var(--backdrop);
    font-family: "Poppins", sans-serif;
  }
  .card {
    position: absolute; left: 248px; width: 704px; height: 402px;
  }
  .card-front { top: 58px; background: var(--rust); }
  .card-back { top: 500px; background: var(--charcoal); color: var(--white); text-align: center; }

  .wordmark {
    position: absolute; left: 0; right: 0;
    text-align: center; font-weight: 400; letter-spacing: 0.06em;
  }
  .card-front .wordmark {
    top: 168px; font-size: 52px; line-height: 64px; color: var(--white);
  }
  .card-back .wordmark {
    top: 44px; font-size: 38px; line-height: 48px; color: var(--rust);
  }

  .name-band {
    position: absolute; left: 130px; right: 130px; top: 137px; height: 78px;
    background: var(--band);
    box-shadow: 0 -8px 14px -6px rgba(0,0,0,.55), 0 8px 14px -6px rgba(0,0,0,.55);
  }
  .person-name {
    position: absolute; left: 0; right: 0; top: 146px;
    font-size: 31px; line-height: 38px; color: var(--rust); font-weight: 400;
  }
  .person-name .first { font-weight: 600; }
  .person-title {
    position: absolute; left: 0; right: 0; top: 182px;
    font-size: 16px; line-height: 22px; font-weight: 500;
  }

  .icon-row {
    position: absolute; left: 0; right: 0; top: 229px;
    display: flex; justify-content: center; gap: 5px;
  }
  .icon { width: 20px; height: 20px; display: block; }
  .contact-line {
    position: absolute; left: 0; right: 0;
    font-size: 18px; line-height: 24px; letter-spacing: 0.03em;
  }
  .phone { top: 256px; }
  .web { top: 280px; }
  .email { top: 304px; }
  .pin-icon { position: absolute; left: 342px; top: 337px; }
  .address { top: 356px; }
</style>
</head>
<body>

<section class="card card-front">
  <div class="wordmark">Dunmere Living</div>
</section>

<section class="card card-back">
  <div class="wordmark">Dunmere Living</div>

  <div class="name-band"></div>
  <div class="person-name"><span class="first">Marta</span> Kovalova</div>
  <div class="person-title">Founder &amp; CEO</div>

  <div class="icon-row">
    <svg class="icon" viewBox="0 0 20 20" aria-label="Phone">
      <circle cx="10" cy="10" r="10" fill="var(--rust)"/>
      <path d="M6.5 5.5 L8.3 5.3 L9 7.8 L8 8.6 C8.6 10 9.8 11.3 11.3 12 L12.1 11 L14.6 11.7 L14.4 13.5 C10 13.8 6.2 10 6.5 5.5 Z" fill="none" stroke="#fff" stroke-width="1.1" stroke-linejoin="round"/>
    </svg>
    <svg class="icon" viewBox="0 0 20 20" aria-label="Email">
      <circle cx="10" cy="10" r="10" fill="var(--rust)"/>
      <rect x="5" y="6.5" width="10" height="7.5" fill="none" stroke="#fff" stroke-width="1.1"/>
      <path d="M5 6.5 L10 10.5 L15 6.5" fill="none" stroke="#fff" stroke-width="1.1"/>
    </svg>
    <svg class="icon" viewBox="0 0 20 20" aria-label="Website">
      <circle cx="10" cy="10" r="10" fill="var(--rust)"/>
      <circle cx="10" cy="10" r="5" fill="none" stroke="#fff" stroke-width="1.1"/>
      <ellipse cx="10" cy="10" rx="2.2" ry="5" fill="none" stroke="#fff" stroke-width="1"/>
      <line x1="5" y1="10" x2="15" y2="10" stroke="#fff" stroke-width="1"/>
    </svg>
  </div>

  <div class="contact-line phone">(555) 014-2290</div>
  <div class="contact-line web">www.www.Dunmere-PK.com</div>
  <div class="contact-line email">info@www.Dunmere-PK.com</div>

  <svg class="icon pin-icon" viewBox="0 0 20 20" aria-label="Address">
    <circle cx="10" cy="10" r="10" fill="var(--rust)"/>
    <path d="M10 15 C7.5 12 6.5 10.5 6.5 8.6 A3.5 3.5 0 0 1 13.5 8.6 C13.5 10.5 12.5 12 10 15 Z" fill="none" stroke="#fff" stroke-width="1.1"/>
    <circle cx="10" cy="8.6" r="1.3" fill="#fff"/>
  </svg>
  <div class="contact-line address">4180 Cedarline Road, Suite #210</div>
</section>

</body>
</html>
```